Facebook Cover Photo & Mailchimp Template for Greyhound Racing Club

Create a consistent, professional visual identity across Facebook and email communications that promotes PWTA as a modern, community-focused greyhound racing club while respecting the heritage of greyhound racing.
Include PWTA logo.
Existing site https://www.socialpage-example.com/WestmereRunners/

```html
<!DOCTYPE html>
<html lang="en">
<head>
<meta charset="UTF-8">
<title>PWTA Racing Club – Race Day Email</title>
<link rel="stylesheet" href="https://fonts.googleapis.com/css2?family=Arimo:wght@400;700&display=swap">
<style>
  :root {
    --page-bg: #f7f7f4;
    --band-green: #1f5a31;
    --heading-green: #2b6a36;
    --button-green: #2e9b33;
    --bullet-green: #2f9a2c;
    --text-dark: #1d1d1d;
    --text-light: #ffffff;
    --photo-light: #ab9076;
    --photo-dark: #987c62;
  }
  * { margin: 0; padding: 0; box-sizing: border-box; }
  html, body {
    width: 1200px; height: 1200px; overflow: hidden;
    background: var(--page-bg);
    font-family: "Arimo", Arial, sans-serif;
    color: var(--text-dark);
  }
  .email { position: relative; width: 1200px; height: 1200px; }

  .header-band {
    position: absolute; left: 35px; top: 35px; width: 1130px; height: 122px;
    background: var(--band-green);
  }
  .brand {
    position: absolute; left: 60px; top: 38px;
    display: flex; align-items: center; gap: 14px;
  }
  .brand-dot { width: 26px; height: 26px; border-radius: 50%; background: var(--bullet-green); }
  .brand-name {
    font-weight: 700; font-size: 34px; letter-spacing: 2px; color: var(--text-light);
  }
  .header-label {
    position: absolute; left: 507px; top: 49px;
    font-weight: 700; font-size: 21px; color: var(--text-light);
  }

  .hero-visual {
    position: absolute; left: 96px; top: 158px; width: 1008px; height: 448px;
    background: linear-gradient(180deg, var(--photo-light) 0%, var(--photo-dark) 100%);
  }

  .headline {
    position: absolute; left: 99px; top: 645px;
    font-weight: 700; font-size: 35px; color: var(--heading-green);
  }
  .intro {
    position: absolute; left: 98px; top: 700px; width: 1000px;
    font-size: 20px; line-height: 30px;
  }

  .whats-on-title {
    position: absolute; left: 98px; top: 801px;
    font-weight: 700; font-size: 23px; color: var(--heading-green);
  }
  .whats-on-list { position: absolute; left: 106px; top: 840px; list-style: none; }
  .whats-on-list li {
    display: flex; align-items: center; gap: 17px;
    font-size: 21px; height: 36px;
  }
  .whats-on-list li::before {
    content: ""; width: 14px; height: 14px; border-radius: 50%;
    background: var(--bullet-green);
  }

  .cta-button {
    position: absolute; left: 96px; top: 937px; width: 481px; height: 61px;
    background: var(--button-green); color: var(--text-light);
    font-weight: 700; font-size: 21px;
    display: flex; align-items: center; justify-content: center;
    text-decoration: none;
  }

  .highlights-label {
    position: absolute; right: 345px; top: 875px; text-align: right;
    font-size: 18px; line-height: 26px;
  }
  .highlights-visual {
    position: absolute; left: 885px; top: 793px; width: 219px; height: 205px;
    background: linear-gradient(180deg, var(--photo-light) 0%, var(--photo-dark) 100%);
  }

  .footer-band {
    position: absolute; left: 35px; top: 1039px; width: 1130px; height: 127px;
    background: var(--band-green); color: var(--text-light);
  }
  .connect-title {
    position: absolute; left: 65px; top: 34px;
    font-weight: 700; font-size: 21px;
  }
  .social-links { position: absolute; left: 65px; top: 68px; display: flex; gap: 9px; }
  .social-links a {
    width: 26px; height: 26px; border-radius: 50%; background: var(--text-light);
    display: block;
  }
  .club-address {
    position: absolute; left: 584px; top: 37px;
    font-size: 16px; line-height: 21px; font-style: normal;
  }
</style>
</head>
<body>
<main class="email">
  <header class="header-band">
    <div class="brand">
      <span class="brand-dot"></span>
      <span class="brand-name">PWTA</span>
    </div>
    <div class="header-label">HERO IMAGE / KEY VISUAL</div>
  </header>

  <div class="hero-visual" role="img" aria-label="Photo of greyhounds racing down a sunlit dirt track toward the camera, with a crowd behind the rail"></div>

  <h1 class="headline">Upcoming Race Day &amp; Community Event!</h1>
  <p class="intro">Join us for an exhilarating day of racing and family fun at Westmere Park! Featuring top-tier racing, food trucks, kids activities, and live music.</p>

  <h2 class="whats-on-title">WHAT’S ON</h2>
  <ul class="whats-on-list">
    <li>Exciting Greyhound Races</li>
    <li>Local Food &amp; Market Stalls</li>
  </ul>

  <a class="cta-button" href="https://www.socialpage-example.com/WestmereRunners/">VIEW RACE SCHEDULE &amp; BUY TICKETS</a>

  <div class="highlights-label">EVENT HIGHLIGHTS<br>PHOTO</div>
  <div class="highlights-visual" role="img" aria-label="Event highlights photo of greyhounds racing on the track"></div>

  <footer class="footer-band">
    <div class="connect-title">CONNECT WITH US</div>
    <nav class="social-links" aria-label="Social links">
      <a href="https://www.socialpage-example.com/WestmereRunners/" aria-label="Social page 1"></a>
      <a href="https://www.socialpage-example.com/WestmereRunners/" aria-label="Social page 2"></a>
      <a href="https://www.socialpage-example.com/WestmereRunners/" aria-label="Social page 3"></a>
      <a href="https://www.socialpage-example.com/WestmereRunners/" aria-label="Social page 4"></a>
    </nav>
    <address class="club-address">PWTA Racing Club.<br>48 Paddock Road, Westmere VIC 3351</address>
  </footer>
</main>
</body>
</html>
```